Tidy paddock Services

After a high quality design website. we are a company that provides services to people that own land and need a hand getting on top of the delayed jobs.
would want a number of tab/ pages for the web page.
Home page / About us page / services page / Gallery page. / Contact us page
we offer a wide range of services .listed below

Stock Work (title)

Stock movement
Break feeding
Temporary staffing

Spraying (title)

Spraying weeds
Spraying gorse

Pastures (title)

Fertilizing
Topping

Building (title)

Habitable sheds
Farm sheds
Sheep yards
Cattle yards
Repair farm buildings
Decks
Retaining walls

Fencing (title)

Stock fencing
Post & rail
Stock yards repair
Electric fencing install & repairs

Water Management (title)

Water trough installation
Water scheme install
Water trough cleaning
Farm water maintenance
Water ponds
Ornamental ponds
Drainage

General (title)

Lawn mowing
Hedge trimming
Pruning trees
Metaling drive ways & races
Water blasting
Small digger work
Little tip truck cartage
Home kill management
Mulching gorse
Section clearing

```html
<!DOCTYPE html>
<html lang="en">
<head>
<meta charset="utf-8">
<title>Tidy paddock Services</title>
<link href="https://fonts.googleapis.com/css2?family=Montserrat:wght@400;500;600;700&display=swap" rel="stylesheet">
<style>
:root{
  --green:#5f9a16;
  --green-dark:#4a7d10;
  --green-light:#7ab51f;
  --black:#000;
  --footer:#111;
  --white:#fff;
  --text:#e9e9e9;
  --grey:#555;
}
*{box-sizing:border-box;margin:0;padding:0}
html,body{width:1200px;height:4121px;overflow:hidden;background:var(--black);font-family:'Montserrat',sans-serif;color:var(--white)}
.page{position:relative;width:1200px;height:4121px;overflow:hidden}
.abs{position:absolute}
.brand{display:flex;align-items:center;gap:12px;font-weight:700;color:var(--green-light);font-size:30px;letter-spacing:.5px}
.brand .dot{width:22px;height:22px;border-radius:50%;background:var(--green-light)}
.topbar{left:595px;top:14px;width:475px;height:46px;border-bottom:1px solid #333;display:flex;align-items:center;justify-content:space-between;font-size:14px}
.topbar .item{display:flex;align-items:center;gap:14px}
.icon-round{width:34px;height:34px;border-radius:50%;border:1.5px solid #444;display:flex;align-items:center;justify-content:center}
.nav{left:584px;top:92px;display:flex;gap:31px;font-size:14px;font-weight:500}
.nav .active{color:var(--green-light)}
.btn{display:flex;align-items:center;justify-content:center;border-radius:30px;font-weight:600;text-transform:uppercase}
.btn-green{background:var(--green);color:var(--white)}
.btn-white{background:var(--white);color:var(--green)}
.hero{left:0;top:142px;width:1200px;height:571px;background:linear-gradient(180deg,#4e6a37 0%,#6a8a47 45%,#8fae5a 80%,#a9c476 100%)}
.hero-person{left:640px;top:150px;width:500px;height:563px;background:radial-gradient(ellipse at 60% 45%,#4f6e9e 0%,#3b5680 40%,rgba(70,100,60,0) 75%)}
.hero h3{left:133px;top:284px;font-size:26px;font-weight:600}
.hero h1{left:133px;top:330px;font-size:52px;font-weight:700;line-height:73px}
.down{left:573px;top:686px;width:54px;height:54px;border-radius:50%;background:var(--white);border:4px solid var(--black);display:flex;align-items:center;justify-content:center}
.title{font-size:28px;font-weight:700;text-transform:uppercase}
.title span{color:var(--green-light)}
.para{font-size:14.5px;line-height:32px;color:var(--text)}
.services-band{left:0;top:1357px;width:1200px;height:565px;background:linear-gradient(135deg,#4d8212 0%,#6aa51d 40%,#5a9416 70%,#467a10 100%);clip-path:polygon(120px 0,1200px 0,1200px 455px,1085px 565px,0 565px,0 90px)}
.card{background:var(--white);color:#333;width:290px;height:435px;top:1422px;text-align:center;padding-top:34px}
.card .ic{width:80px;height:80px;margin:0 auto;border-radius:50%;background:var(--green);display:flex;align-items:center;justify-content:center;box-shadow:0 0 0 3px #fff,0 0 0 5px var(--green)}
.card h4{color:var(--green);font-size:22px;font-weight:600;margin-top:32px}
.card p{font-size:14.5px;line-height:32px;padding:0 30px;margin-top:10px;color:#444}
.card .btn{width:136px;height:38px;font-size:14px;margin:14px auto 0}
.photo{position:absolute}
.step-ic{position:absolute;width:90px;height:90px;border-radius:50%;border:2px solid var(--green)}
.step-ic .num{position:absolute;right:-12px;top:-4px;width:28px;height:28px;border-radius:50%;background:var(--white);color:var(--green);font-size:12px;font-weight:700;display:flex;align-items:center;justify-content:center}
.step-ic.left .num{left:-12px;right:auto}
.step h5{color:var(--green-light);font-size:16px;font-weight:600}
.step p{font-size:15px;line-height:32px;margin-top:8px}
.contact-lower{left:0;top:3715px;width:1200px;height:406px;background:var(--footer)}
.contact{left:138px;top:3423px;width:924px;height:399px;background:var(--green);border-radius:26px}
.field{position:absolute;background:#fafafa;border-radius:5px;color:#333;font-size:13px;font-weight:500;padding:0 14px;display:flex;align-items:center;justify-content:space-between}
.footnav{left:0;top:4016px;width:1200px;display:flex;justify-content:center;gap:14px;font-size:15px}
</style>
</head>
<body>
<div class="page">

<!-- header -->
<div class="abs brand" style="left:135px;top:48px"><span class="dot"></span>TIDY PADDOCK SERVICES</div>
<div class="abs topbar">
  <div class="item"><div class="icon-round"><svg width="16" height="16" viewBox="0 0 24 24"><path d="M6 3l4 4-2 3a12 12 0 006 6l3-2 4 4-3 3C10 21 3 14 3 6z" fill="none" stroke="#7ab51f" stroke-width="2"/></svg></div>+1 555 010 2040</div>
  <div class="item"><div class="icon-round"><svg width="16" height="16" viewBox="0 0 24 24"><rect x="3" y="6" width="18" height="12" fill="#7ab51f"/><path d="M3 6l9 7 9-7" stroke="#000" stroke-width="1.5" fill="none"/></svg></div>HELLO@TIDYPADDOCK.CO</div>
</div>
<div class="abs nav"><span class="active">HOME</span><span>ABOUT US</span><span>SERVICES</span><span>GALLERY</span><span>CONTACT US</span></div>

<!-- hero -->
<div class="abs hero" role="img" aria-label="Hedge rows and grass field in soft focus"></div>
<div class="abs hero-person" role="img" aria-label="Man kneeling on grass using a hand pressure sprayer"></div>
<svg class="abs" style="left:640px;top:200px" width="240" height="420" viewBox="0 0 240 420"><path d="M230 10 C 90 20, 20 170, 110 300 C 140 340, 180 370, 220 390" fill="none" stroke="#fff" stroke-width="14" stroke-linecap="round"/></svg>
<h3 class="abs hero h3" style="position:absolute;left:133px;top:284px;font-size:26px;font-weight:600;background:none;width:auto;height:auto">WELCOME TO</h3>
<h1 class="abs" style="left:133px;top:330px;font-size:52px;font-weight:700;line-height:73px">TIDY PADDOCK<br>SERVICES</h1>
<div class="abs btn btn-green" style="left:133px;top:505px;width:214px;height:60px;font-size:22px">Get Started</div>
<div class="abs down"><svg width="20" height="20" viewBox="0 0 24 24"><path d="M5 9l7 7 7-7" fill="none" stroke="#000" stroke-width="2.5"/></svg></div>

<!-- about -->
<svg class="abs" style="left:170px;top:825px" width="450" height="450" viewBox="0 0 450 450">
  <path d="M225 3 A222 222 0 1 1 12 290" fill="none" stroke="#fff" stroke-width="3"/>
  <path d="M30 140 A222 222 0 0 1 225 3" fill="none" stroke="#5f9a16" stroke-width="3"/>
</svg>
<div class="abs" role="img" aria-label="Hand holding fertiliser granules over soil beside a potted plant" style="left:206px;top:861px;width:380px;height:380px;border-radius:50%;background:radial-gradient(circle at 65% 40%,#5c8a2c 0%,#3f5d22 35%,#4a3424 65%,#2f2118 100%)"></div>
<h2 class="abs title" style="left:706px;top:830px">About <span>Us</span></h2>
<p class="abs para" style="left:678px;top:903px;width:370px">Lorem ipsum dolor sit amet, consectetur adipiscing elit, sed do eiusmod tempor incididunt ut labore et dolore magna aliqua. Ut enim ad minim veniam, quis nostrud exercitation ullamco laboris nisi ut aliquip ex ea commodo consequat. Duis aute irure dolor in reprehenderit in voluptate velit esse cillum dolore eu fugiat nulla pariatur. Excepteur sint occaecat cupidatat.</p>
<div class="abs btn btn-green" style="left:678px;top:1198px;width:190px;height:56px;font-size:20px">Learn More</div>

<!-- services -->
<div class="abs services-band"></div>
<h2 class="abs title" style="left:160px;top:1475px">Our Services</h2>
<p class="abs para" style="left:132px;top:1547px;width:305px;color:#fff">Lorem ipsum dolor sit amet, consectetur adipiscing elit, sed do eiusmod tempor incididunt ut labore et dolore magna aliqua. Ut enim ad minim veniam, quis nostrud exercitation.</p>
<div class="abs btn btn-white" style="left:132px;top:1736px;width:206px;height:56px;font-size:20px">View Services</div>
<div class="abs card" style="left:475px">
  <div class="ic"><svg width="40" height="40" viewBox="0 0 24 24" fill="none" stroke="#fff" stroke-width="1.5"><circle cx="8" cy="8" r="3"/><circle cx="16" cy="8" r="3"/><circle cx="12" cy="14" r="4"/><path d="M15 17l4 4"/></svg></div>
  <h4>STOCK WORK</h4>
  <p>Lorem ipsum dolor sit amet, consectetur adipiscing elit, sed do eiusmod tempor incididunt ut labore et dolore magna aliqua.</p>
  <div class="btn btn-green">Read More</div>
</div>
<div class="abs card" style="left:780px">
  <div class="ic"><svg width="40" height="40" viewBox="0 0 24 24" fill="none" stroke="#fff" stroke-width="1.5"><path d="M12 4v8M8 5l2 7M16 5l-2 7"/><rect x="9" y="12" width="6" height="4"/><path d="M4 19h16M12 16v3"/></svg></div>
  <h4>SPRAYING</h4>
  <p>Lorem ipsum dolor sit amet, consectetur adipiscing elit, sed do eiusmod tempor incididunt ut labore et dolore magna aliqua.</p>
  <div class="btn btn-green">Read More</div>
</div>

<!-- gallery -->
<h2 class="abs title" style="left:0;top:2016px;width:1200px;text-align:center">Our <span>Gallery</span></h2>
<div class="photo" role="img" aria-label="Lawn mower cutting grass at sunset" style="left:203px;top:2125px;width:251px;height:341px;background:linear-gradient(160deg,#d9a95a,#6f7f3a 55%,#3b5a22)"></div>
<div class="photo" role="img" aria-label="Black metal fence along a grass verge" style="left:477px;top:2125px;width:251px;height:217px;background:linear-gradient(180deg,#2f4a24,#4f7a30 60%,#6d9a3e)"></div>
<div class="photo" role="img" aria-label="Worker in protective suit spraying weeds" style="left:746px;top:2125px;width:251px;height:340px;background:linear-gradient(120deg,#e5e5e5 0%,#9fae7a 35%,#5d7a3a 100%)"></div>
<div class="photo" role="img" aria-label="Weeds along a fence line beside a path" style="left:203px;top:2487px;width:251px;height:215px;background:linear-gradient(90deg,#efe9dc 0%,#b8b09c 45%,#6c7d48 100%)"></div>
<div class="photo" role="img" aria-label="Scoop spreading fertiliser around young plants" style="left:477px;top:2365px;width:251px;height:337px;background:linear-gradient(180deg,#4c7a33,#3a4d27 55%,#4a3a2c)"></div>
<div class="photo" role="img" aria-label="Rows of crops stretching to the horizon" style="left:746px;top:2488px;width:251px;height:214px;background:linear-gradient(180deg,#f0c99a 0%,#b7c3a7 30%,#3e6b2a 45%,#2f4d1d 100%)"></div>
<div class="photo" role="img" aria-label="Kneeling worker figure with sprayer" style="left:88px;top:2530px;width:112px;height:130px;background:#e9e9e9;border-radius:14px"></div>
<div class="photo" role="img" aria-label="Kneeling worker figure with sprayer" style="left:1000px;top:2530px;width:112px;height:130px;background:#e9e9e9;border-radius:14px"></div>

<!-- steps -->
<h2 class="abs title" style="left:0;top:2800px;width:1200px;text-align:center">What are the steps to <span>Get Started</span></h2>
<div class="step-ic" style="left:156px;top:2910px"><span class="num">01</span><svg width="86" height="86" viewBox="0 0 86 86" fill="none" stroke="#fff" stroke-width="2"><circle cx="43" cy="30" r="6"/><path d="M43 36v18M33 46l10-6 10 6M36 66l7-12 7 12"/></svg></div>
<div class="abs step" style="left:307px;top:2927px"><h5>YOU MAKE THE FIRST MOVE</h5><p>Lorem ipsum dolor sit amet,<br>consectetur adipiscing elit</p></div>
<div class="step-ic left" style="left:146px;top:3055px"><span class="num">02</span><svg width="86" height="86" viewBox="0 0 86 86" fill="none" stroke="#fff" stroke-width="2"><circle cx="30" cy="36" r="5"/><circle cx="43" cy="32" r="5"/><circle cx="56" cy="36" r="5"/><path d="M24 58v-8h38v8"/></svg></div>
<div class="abs step" style="left:272px;top:3071px"><h5>WE UNDERSTAND EACH OTHER</h5><p>Lorem ipsum dolor sit amet,<br>consectetur adipiscing elit</p></div>
<div class="step-ic" style="left:156px;top:3200px"><span class="num" style="top:34px">03</span><svg width="86" height="86" viewBox="0 0 86 86" fill="none" stroke="#fff" stroke-width="2"><circle cx="43" cy="46" r="12"/><path d="M30 26l3 3M43 22v4M56 26l-3 3"/></svg></div>
<div class="abs step" style="left:307px;top:3215px"><h5>YOU DECIDE THE NEXT MOVE</h5><p>Lorem ipsum dolor sit amet,<br>consectetur adipiscing elit</p></div>
<svg class="abs" style="left:120px;top:2990px" width="90" height="230" viewBox="0 0 90 230" fill="none" stroke="#fff" stroke-width="1.5"><path d="M76 42c-2 10-6 16-12 20M64 62l1-6M64 62l6-2"/><path d="M80 190c4-8 4-16-2-22M78 168l-1 6M78 168l-6 2" transform="translate(-5,-10)"/></svg>
<svg class="abs" style="left:585px;top:2904px" width="500" height="470" viewBox="0 0 500 470">
  <path d="M410 80 A218 218 0 1 1 130 62" fill="none" stroke="#fff" stroke-width="3"/>
  <path d="M130 62 A218 218 0 0 1 410 80" fill="none" stroke="#5f9a16" stroke-width="3"/>
</svg>
<div class="abs" role="img" aria-label="Close-up of fresh green lawn" style="left:615px;top:3015px;width:376px;height:376px;border-radius:50%;background:linear-gradient(180deg,#b7c9d3 0%,#8aa7b0 30%,#5f9a16 55%,#2f5a10 100%)"></div>

<!-- contact -->
<div class="abs contact-lower"></div>
<div class="abs contact"></div>
<h2 class="abs" style="left:0;top:3465px;width:1200px;text-align:center;font-size:28px;font-weight:600">CONTACT US</h2>
<div class="field" style="left:154px;top:3540px;width:218px;height:50px">FIRST NAME<svg width="14" height="14" viewBox="0 0 24 24" fill="none" stroke="#5f9a16" stroke-width="2"><circle cx="12" cy="8" r="4"/><path d="M4 21c1-5 15-5 16 0"/></svg></div>
<div class="field" style="left:379px;top:3540px;width:218px;height:50px">LAST NAME<svg width="14" height="14" viewBox="0 0 24 24" fill="none" stroke="#5f9a16" stroke-width="2"><circle cx="12" cy="8" r="4"/><path d="M4 21c1-5 15-5 16 0"/></svg></div>
<div class="field" style="left:604px;top:3540px;width:218px;height:50px">EMAIL ADDRESS<svg width="15" height="14" viewBox="0 0 24 24" fill="none" stroke="#5f9a16" stroke-width="2"><rect x="3" y="6" width="18" height="12"/><path d="M3 6l9 7 9-7"/></svg></div>
<div class="field" style="left:829px;top:3540px;width:218px;height:50px">PHONE NUMBER<svg width="14" height="14" viewBox="0 0 24 24" fill="none" stroke="#5f9a16" stroke-width="2"><path d="M6 3l4 4-2 3a12 12 0 006 6l3-2 4 4-3 3C10 21 3 14 3 6z"/></svg></div>
<div class="field" style="left:154px;top:3600px;width:893px;height:93px;align-items:flex-start;padding-top:14px">MESSAGE<svg width="16" height="15" viewBox="0 0 24 24" fill="none" stroke="#5f9a16" stroke-width="2"><path d="M3 4h18v12H9l-5 4v-4H3z"/></svg></div>
<div class="abs btn btn-white" style="left:497px;top:3723px;width:206px;height:56px;font-size:20px">Submit Now</div>

<!-- footer -->
<div class="abs brand" style="left:0;top:3908px;width:1200px;justify-content:center"><span class="dot"></span>TIDY PADDOCK SERVICES</div>
<div class="abs footnav"><span>HOME</span><span>|</span><span>ABOUT US</span><span>|</span><span>SERVICE</span><span>|</span><span>GALLERY</span><span>|</span><span>CONTACT US</span></div>
<div class="abs" style="left:0;top:4068px;width:1200px;text-align:center;font-size:14px">@2024 COPYRIGHTS - ALL RIGHTS RESERVED</div>

</div>
</body>
</html>
```